Brightline Energy Product Distribution Brochure

We are looking to have our current brochure for our customers completely redesigned...the idea is to present the relevant information in an attractive way . Our website is brightlineenergyco.example where you can find more information about us. We have included a file with a rough idea of the page order and what each should include but feel free to adapt based on design. The example provided is only for context and doesnt have to be maintained. We will be using the brochure both digitally and in print form. As long as it reads easily and is eye catching, the design can be horizontal or vertical.Final deliverable should be indesign file.

"Our Brands" page: should be limited to one page (space being enough) where it has the header for each one (for example diesel generators) space for one or two lines of text and then the corresponding logos for each of the five categories
Updates

For those asking: the "our brands" page should be a single page layout where there is a header with the corresponding section and space for maybe one line of text followed by the two logos for that category. Each of the product pages should be similar in fashion to the one in the document attached: a photo of the product with some white space and space for the text to be included. We will be posting additional examples today

Target Market(s)

We want to present it to customers both digitally and in print so they can see our products

Industry/Entity Type

Power Generation

Font styles to use
Serif

Requirements
Must have
• Eye catching and able to present the information in a presentable fashion. Rest is up to you.
Nice to have
• Should incorporate the colors of our logo but can also add other depending on design

```html
<!DOCTYPE html>
<html lang="en">
<head>
<meta charset="utf-8">
<title>Brightline Energy – Alternator Parts Spread</title>
<link rel="stylesheet" href="https://fonts.googleapis.com/css2?family=Michroma&family=Montserrat:wght@400;800&display=swap">
<style>
  :root {
    --canvas: #e6e4df;
    --paper: #ffffff;
    --yellow: #f2b705;
    --yellow-light: #f7cf2a;
    --red: #d62a1e;
    --ink: #141414;
    --body: #8a8a8a;
    --bullet: #e6ebf2;
  }
  * { margin: 0; padding: 0; box-sizing: border-box; }
  html, body { width: 1200px; height: 960px; overflow: hidden; background: var(--canvas); }

  .spread {
    position: absolute; left: 40px; top: 250px; width: 1120px; height: 460px;
    background: var(--paper);
    box-shadow: 0 18px 40px rgba(0,0,0,.18);
    font-family: "Montserrat", sans-serif;
    overflow: hidden;
  }

  /* Full-bleed generator photograph cut on the diagonal */
  .hero-photo {
    position: absolute; inset: 0;
    clip-path: polygon(250px 0, 1055px 0, 1120px 80px, 1120px 460px, 690px 460px, 545px 300px);
    background:
      radial-gradient(ellipse 260px 200px at 880px 120px, rgba(88,120,160,.55), rgba(88,120,160,0) 70%),
      radial-gradient(ellipse 220px 170px at 760px 300px, rgba(70,104,146,.6), rgba(70,104,146,0) 70%),
      radial-gradient(ellipse 200px 160px at 1060px 400px, rgba(120,84,40,.55), rgba(120,84,40,0) 70%),
      radial-gradient(ellipse 260px 140px at 470px 160px, rgba(40,40,40,.9), rgba(40,40,40,0) 70%),
      linear-gradient(100deg, #07090c 0%, #0f1620 35%, #1e334d 60%, #2c4a6e 82%, #223852 100%);
  }

  .spine {
    position: absolute; left: 552px; top: 0; width: 22px; height: 460px;
    background: linear-gradient(90deg, rgba(0,0,0,0), rgba(0,0,0,.14) 50%, rgba(0,0,0,0));
  }

  .section-tab {
    position: absolute; left: 52px; top: 0; width: 40px; height: 44px;
    background: var(--yellow);
    color: #fff; font-family: "Michroma", sans-serif; font-size: 10px;
    display: flex; align-items: flex-end; justify-content: center; padding-bottom: 10px;
  }
  .section-band {
    position: absolute; left: 52px; top: 62px; width: 468px; height: 62px;
    background: linear-gradient(90deg, var(--yellow-light), var(--yellow));
    color: #fff; font-family: "Michroma", sans-serif; font-weight: 400; font-size: 20px; letter-spacing: 1px;
    display: flex; align-items: center; justify-content: center;
  }

  .brand-row {
    position: absolute; left: 52px; top: 196px; display: flex; align-items: center; gap: 8px;
    font-weight: 800; font-size: 13px; color: var(--red); text-transform: uppercase;
  }
  .brand-row .divider { width: 1px; height: 11px; background: #b8b8b8; }
  .brand-stack {
    position: absolute; left: 52px; top: 226px;
    font-weight: 800; font-size: 18px; line-height: 1.15; color: var(--ink); text-transform: uppercase;
  }
  .intro {
    position: absolute; left: 52px; top: 282px; width: 196px;
    font-size: 7.5px; line-height: 1.6; color: var(--body);
  }
  .intro p + p { margin-top: 3px; }

  .product-shot {
    position: absolute; left: 276px; top: 188px; width: 290px; height: 220px;
    background:
      radial-gradient(ellipse 60px 80px at 30% 52%, rgba(150,120,70,.75), rgba(150,120,70,0) 80%),
      radial-gradient(ellipse 48% 46% at 50% 50%, #3a3a3a 0%, #222 55%, rgba(34,34,34,.6) 80%, rgba(34,34,34,0) 100%);
  }

  .feature-lists {
    position: absolute; left: 710px; top: 378px; display: flex; gap: 30px;
  }
  .feature-list {
    list-style: none;
    font-size: 8.5px; line-height: 1.65; color: var(--bullet);
  }
  .feature-list li::before { content: "• "; }
</style>
</head>
<body>
  <section class="spread">
    <div class="hero-photo" role="img" aria-label="Close-up photograph of a blue industrial diesel generator housing with ventilation grille and black alternator casing"></div>
    <div class="spine"></div>

    <div class="section-tab">AP</div>
    <h1 class="section-band">Alternator Parts</h1>

    <div class="brand-row"><span>Halden</span><span class="divider"></span><span>Korvex</span></div>
    <div class="brand-stack">Marlow<br>Tessier</div>

    <div class="intro">
      <p>Genuine alternator parts sourced directly from leading manufacturers, ready to ship for service, repair and upgrade work. Every component is checked before dispatch so your equipment returns to duty quickly.</p>
      <p>Our team helps you match rotors, stators, regulators and bearings to your exact frame size, keeping downtime short and output steady across every site you run.</p>
    </div>

    <div class="product-shot" role="img" aria-label="Product photograph of a black industrial alternator with exposed coupling disc"></div>

    <div class="feature-lists">
      <ul class="feature-list">
        <li>Stators and rotors for all frames</li>
        <li>Voltage regulators in stock</li>
        <li>Bearings and couplings ready</li>
        <li>Fast nationwide delivery</li>
      </ul>
      <ul class="feature-list">
        <li>Factory original components</li>
        <li>Expert matching support on call</li>
        <li>Tested before every shipment</li>
        <li>Warranty on parts</li>
      </ul>
    </div>
  </section>
</body>
</html>
```